Veltrane Group Business Card Design

The CEO is looking for a new trendy look for his business card.
You can stay with current branding or come up with something new/creative. It can be 3D, including Medical Office buildings. You can use our logo in a variety of colors. Please include name, title, company name, company website, email address, cell number

Target Market(s)

Real Estate Development and Construction

Industry/Entity Type

Health care real estate

Contact Information for Business Card

Rohesh Kamdar, CEO M-604.781.2249 E-roheshkamdar@veltrane.com Address:4180 Lindqvist Ave, Tampa, FL 33482 www.veltrane.com

Font styles to use
Other font styles liked:
• Be creative

Requirements
Must have
• Creative, trendy look
Nice to have
• Please go to our website to get a feel- www. veltrane.com
Should not have
• small fonts

```html
<!DOCTYPE html>
<html lang="en">
<head>
<meta charset="utf-8">
<title>Veltrane Group – Business Card</title>
<link href="https://fonts.googleapis.com/css2?family=Poppins:wght@300;400;700;800&display=swap" rel="stylesheet">
<style>
  :root {
    --bg: #26272a;
    --card-red: #b31e28;
    --pattern-dark: #8e1820;
    --pattern-light: #c92630;
    --ink: #ffffff;
    --rule: rgba(255,255,255,0.8);
  }
  * { margin: 0; padding: 0; box-sizing: border-box; }
  html, body {
    width: 1200px; height: 1108px; overflow: hidden;
    background: var(--bg);
    font-family: "Poppins", sans-serif;
    color: var(--ink);
  }
  .stage { position: relative; width: 1200px; height: 1108px; }
  .card {
    position: absolute; top: 164px;
    width: 440px; height: 780px;
    border-radius: 26px;
    background: var(--card-red);
    overflow: hidden;
    box-shadow: 0 18px 40px rgba(0,0,0,0.45);
  }
  .card--front { left: 110px; }
  .card--back { left: 650px; }

  .brand {
    position: absolute; top: 110px; left: 0; right: 0;
    text-align: center; font-weight: 800; line-height: 0.95;
  }
  .brand__name { font-size: 84px; letter-spacing: -3px; display: block; }
  .brand__group { font-size: 46px; display: block; padding-left: 170px; }

  .contact {
    position: absolute; top: 440px; left: 0; right: 0;
    text-align: center;
  }
  .contact__name { font-size: 32px; font-weight: 700; line-height: 1.1; }
  .contact__title { font-size: 22px; font-weight: 300; margin-top: 2px; }
  .icon-row {
    display: flex; align-items: center; justify-content: center;
    gap: 8px; margin: 10px 0 12px;
  }
  .icon-row__rule { width: 70px; height: 1px; background: var(--rule); }
  .icon { width: 38px; height: 38px; }
  .contact__line { font-size: 21px; font-weight: 300; line-height: 1.45; }
  .contact__divider { width: 290px; height: 1px; background: var(--rule); margin: 12px auto; }
  .contact__address { font-size: 21px; font-weight: 300; line-height: 1.4; }

  .pattern {
    position: absolute; inset: 0;
    background:
      repeating-linear-gradient(-20deg, var(--pattern-dark) 0 22px, var(--card-red) 22px 60px),
      var(--card-red);
    opacity: 0.55;
  }
  .back-mark {
    position: absolute; left: 0; right: 0; top: 500px;
    text-align: center; font-weight: 800; line-height: 0.95;
  }
  .back-mark__name { font-size: 40px; letter-spacing: -1px; display: block; }
  .back-mark__group { font-size: 22px; display: block; padding-left: 80px; }
</style>
</head>
<body>
<main class="stage">
  <section class="card card--front" aria-label="Business card front">
    <div class="brand">
      <span class="brand__name">Veltrane</span>
      <span class="brand__group">Group</span>
    </div>
    <div class="contact">
      <p class="contact__name">Rohesh Kamdar</p>
      <p class="contact__title">CEO</p>
      <div class="icon-row">
        <span class="icon-row__rule"></span>
        <svg class="icon" viewBox="0 0 38 38" aria-label="Phone">
          <rect x="1" y="1" width="36" height="36" rx="6" fill="#fff"/>
          <path d="M12 11c2-2 4 0 5 2s-1 3-1 4c1 2 3 4 5 5 1 0 2-2 4-1s4 3 2 5c-2 2-6 2-10-2s-7-9-5-13z" fill="var(--card-red)"/>
        </svg>
        <svg class="icon" viewBox="0 0 38 38" aria-label="Email">
          <rect x="1" y="1" width="36" height="36" rx="6" fill="#fff"/>
          <rect x="8" y="12" width="22" height="15" rx="1.5" fill="none" stroke="var(--card-red)" stroke-width="2.2"/>
          <path d="M8 13l11 8 11-8" fill="none" stroke="var(--card-red)" stroke-width="2.2"/>
        </svg>
        <svg class="icon" viewBox="0 0 38 38" aria-label="Website">
          <rect x="1" y="1" width="36" height="36" rx="6" fill="#fff"/>
          <circle cx="19" cy="19" r="10" fill="none" stroke="var(--card-red)" stroke-width="2.2"/>
          <ellipse cx="19" cy="19" rx="4.5" ry="10" fill="none" stroke="var(--card-red)" stroke-width="1.8"/>
          <path d="M9 19h20" stroke="var(--card-red)" stroke-width="1.8"/>
        </svg>
        <span class="icon-row__rule"></span>
      </div>
      <p class="contact__line">604.781.2249</p>
      <p class="contact__line">roheshkamdar@veltrane.com</p>
      <p class="contact__line">www.veltrane.com</p>
      <div class="contact__divider"></div>
      <p class="contact__address">4180 Lindqvist Ave, Tampa<br>FL 33482</p>
    </div>
  </section>

  <section class="card card--back" aria-label="Business card back">
    <div class="pattern" role="img" aria-label="Tonal red pattern of repeated company name"></div>
    <div class="back-mark">
      <span class="back-mark__name">Veltrane</span>
      <span class="back-mark__group">Group</span>
    </div>
  </section>
</main>
</body>
</html>
```